Oil Field Service company needs professional business cards

Looking to clean up our current company business cards and look a little more professional. Brenwick Casing Services is a US based company that services the oil field. We deal with engineers, managers and oil rigs....................................................................................................................................................................................................................................................................................................................................................................................................

Target Market(s)

Oil and Gas professionals

Industry/Entity Type

Oil And Gas

Contact Information for Business Card

See attached photo as example

Font styles to use
Sans Serif

Colors
ec1f27

Requirements
Must have
• Company Logo, Name, Title, Cell, Office, Fax, Email.
• See attached photo
Nice to have
• External CRT, Internal CRT, Casing Crews, Torque Turn, Laydown Machine
Should not have
• Do not introduce any new pictures and keep it professional looking

```html
<!DOCTYPE html>
<html lang="en">
<head>
<meta charset="utf-8">
<title>Brenwick Casing Services – Business Card</title>
<link href="https://fonts.googleapis.com/css2?family=Open+Sans:wght@400;600;700&display=swap" rel="stylesheet">
<style>
  :root {
    --brand-red: #ec1f27;
    --brand-red-deep: #c8141c;
    --slate: #3c4650;
    --ink: #222222;
    --card-white: #fbfbfb;
    --backdrop: #e6e6e6;
    --white: #ffffff;
  }
  html, body {
    margin: 0;
    width: 1200px;
    height: 900px;
    overflow: hidden;
    background: var(--backdrop);
    font-family: "Open Sans", Arial, sans-serif;
  }
  .card {
    position: absolute;
    left: 112px;
    top: 150px;
    width: 975px;
    height: 600px;
    border-radius: 30px;
    background: var(--card-white);
    overflow: hidden;
    box-shadow: 0 6px 24px rgba(0,0,0,0.12);
  }
  .card__sweep {
    position: absolute;
    inset: 0;
    width: 975px;
    height: 600px;
  }
  .brand-name {
    position: absolute;
    left: 52px;
    top: 96px;
    margin: 0;
    color: var(--slate);
    font-weight: 700;
    font-size: 44px;
    line-height: 1.15;
    letter-spacing: 2px;
    text-transform: uppercase;
  }
  .person {
    position: absolute;
    left: 52px;
    top: 396px;
  }
  .person__name {
    margin: 0;
    color: var(--brand-red);
    font-weight: 700;
    font-size: 34px;
    line-height: 1.2;
  }
  .person__title {
    margin: 2px 0 0;
    color: var(--ink);
    font-size: 24px;
  }
  .person__address {
    position: absolute;
    left: 52px;
    top: 510px;
    margin: 0;
    color: var(--ink);
    font-size: 24px;
  }
  .services, .contacts {
    position: absolute;
    right: 43px;
    margin: 0;
    padding: 0;
    list-style: none;
    color: var(--white);
    text-align: right;
  }
  .services {
    top: 168px;
    font-size: 26px;
    line-height: 36px;
  }
  .services li::after {
    content: "";
    display: inline-block;
    width: 12px;
    height: 12px;
    margin-left: 14px;
    border-radius: 50%;
    background: var(--white);
    vertical-align: 2px;
  }
  .contacts {
    top: 410px;
    font-size: 25px;
    line-height: 35px;
  }
  .contacts li {
    display: flex;
    justify-content: flex-end;
    align-items: center;
  }
  .contacts svg {
    width: 16px;
    height: 16px;
    margin-left: 10px;
    fill: var(--white);
  }
</style>
</head>
<body>
  <article class="card">
    <svg class="card__sweep" viewBox="0 0 975 600" aria-hidden="true">
      <defs>
        <linearGradient id="sweepFill" x1="0" y1="0" x2="1" y2="1">
          <stop offset="0" stop-color="var(--brand-red)"/>
          <stop offset="1" stop-color="var(--brand-red-deep)"/>
        </linearGradient>
      </defs>
      <path d="M825,0 Q450,225 338,600 L975,600 L975,0 Z" fill="url(#sweepFill)"/>
    </svg>

    <h1 class="brand-name">Brenwick<br>Casing Services</h1>

    <div class="person">
      <p class="person__name">Cody Harlan</p>
      <p class="person__title">Area Manager</p>
    </div>
    <p class="person__address">Redmesa,&nbsp; OK 73899</p>

    <ul class="services">
      <li>External CRT</li>
      <li>Internal CRT</li>
      <li>Casing Crews</li>
      <li>Torque Turn</li>
      <li>Laydown Machine</li>
    </ul>

    <ul class="contacts">
      <li>(580) 555-0142
        <svg viewBox="0 0 16 16" aria-label="Office"><path d="M2 5c0-2 2-3 6-3s6 1 6 3v1h-3V5H5v1H2zM4 7h8l2 7H2z"/></svg>
      </li>
      <li>(580) 555-0187
        <svg viewBox="0 0 16 16" aria-label="Fax"><path d="M4 1h6l2 2v3H4zM2 7h12v8H2zm3 2v1h2V9zm4 0v1h2V9zm-4 2v1h2v-1zm4 0v1h2v-1z"/></svg>
      </li>
      <li>(580) 555-0163
        <svg viewBox="0 0 16 16" aria-label="Cell"><path d="M5 1h6a1 1 0 0 1 1 1v12a1 1 0 0 1-1 1H5a1 1 0 0 1-1-1V2a1 1 0 0 1 1-1zm0 2v9h6V3zm3 10a.8.8 0 1 0 0 1.6A.8.8 0 0 0 8 13z"/></svg>
      </li>
      <li>codyharlan@brenwickcasing.com
        <svg viewBox="0 0 16 16" aria-label="Email"><path d="M1 3h14v10H1zm1.5 1.5L8 9l5.5-4.5z"/></svg>
      </li>
    </ul>
  </article>
</body>
</html>
```